CalmPeak Nurses' Manifesto

Design a manifesto to inspire and motivate nurses to work at minimum standards of excellence in their nursing practice.

The manifesto will become a feature of our website, at conferences, workshops and retreats. It will also be featured on other marketing tools.

Primary Market:
Nurses and/or other healthcare professionals (specifically Doctors, Occupational Therapists, Psychologists and Social Workers).

However the manifesto is equally applicable to all nurses and healthcare professionals from new graduates to very experienced senior clinicians, administration officers,managers and healthcare executive personnel.

Mainly females and primarily 35 to 65 years old, which suggests people in this target age group have extensive experience, but have become jaded'.

The purpose of our business is to assist healthcare professionals, primarily nurses, to maintain their enthusiasm and excellence in service provision, for their benefit as well as the benefit of the clients.

I have attached:
File 1: Copy Samples and examples: which has the copy for the manifesto, examples that appeal to us and our 3 attempts.
File 2: Our colour Spec Sheet, HOWEVER the colours are not necessary limited to these colours. These colours are not in the logo that will be on the manifesto. The colours on the logo attached can/or also be used.
File 3: Prototype logo. The final logo will be available within 3 to 4 days.

Industry/Entity Type

Healthcare

Requirements
Must have
• Must use the copy as per the attached file.

It should be contemporary, eye catching and motivational.

Should not have
• MUST BE EASY TO READ. Each line MUST be clearly defined from each other.

```html
<!DOCTYPE html>
<html lang="en">
<head>
<meta charset="utf-8">
<title>CalmPeak – A Nurses' Manifesto</title>
<link rel="stylesheet" href="https://fonts.googleapis.com/css2?family=Cabin+Condensed:wght@500;600&family=Tenor+Sans&family=Cabin:wght@500&display=swap">
<style>
  :root {
    --red: #e8202a;
    --white: #ffffff;
    --ink: #231f20;
    --wide: "Tenor Sans", sans-serif;
    --narrow: "Cabin Condensed", sans-serif;
  }
  * { margin: 0; padding: 0; box-sizing: border-box; }
  html, body { width: 848px; height: 1200px; overflow: hidden; background: var(--red); }
  .manifesto {
    position: relative; width: 848px; height: 1200px;
    background: var(--red); color: var(--white);
    font-family: var(--wide); line-height: 1;
  }
  .manifesto > * { position: absolute; white-space: nowrap; }
  .wide { font-family: var(--wide); -webkit-text-stroke: 1.1px var(--white); }
  .narrow { font-family: var(--narrow); font-weight: 600; }
  .small { -webkit-text-stroke: 0.4px var(--white); }
  .band {
    background: var(--white); color: var(--red);
    font-family: var(--wide); -webkit-text-stroke: 1.2px var(--red);
    display: flex; align-items: center; justify-content: center;
    border-radius: 12px;
  }
  .brand-box {
    left: 445px; top: 0; width: 403px; height: 188px;
    background: var(--white); border-radius: 0 0 0 28px;
    display: flex; flex-direction: column; align-items: center; justify-content: center; gap: 26px;
    color: var(--ink);
  }
  .brand-name { font-family: var(--narrow); font-weight: 600; font-size: 38px; color: var(--ink); display: flex; align-items: center; gap: 10px; }
  .brand-dot { width: 18px; height: 18px; border-radius: 50%; background: var(--red); }
  .brand-tag { font-family: "Cabin", sans-serif; font-weight: 500; font-size: 23px; }
</style>
</head>
<body>
<main class="manifesto">

  <div class="brand-box">
    <div class="brand-name"><span class="brand-dot"></span>CalmPeak</div>
    <div class="brand-tag">A Nurses' Manifesto</div>
  </div>

  <h1 class="narrow" style="left:38px;top:24px;font-size:110px;font-weight:500;">NURSE</h1>
  <p class="narrow" style="left:40px;top:140px;font-size:31px;font-weight:500;">WITH OPEN <span style="font-size:44px">HANDS,</span></p>
  <p class="narrow" style="left:38px;top:180px;font-size:54px;font-weight:500;letter-spacing:2px;">HEARTS &amp; MINDS</p>

  <p class="wide small" style="left:40px;top:246px;font-size:18px;line-height:1.3;">DELIGHT YOUR CLIENTS<br>&amp; COLLEAGUES BY<br>EXCEEDING THEIR</p>
  <svg class="cap-icon" style="left:228px;top:280px" width="68" height="34" viewBox="0 0 68 34" aria-hidden="true">
    <path d="M4 30 Q4 4 34 2 Q64 4 64 30 Z" fill="var(--white)"/>
    <rect x="30" y="8" width="8" height="18" fill="var(--red)"/>
    <rect x="25" y="13" width="18" height="8" fill="var(--red)"/>
  </svg>
  <p class="wide" style="left:40px;top:335px;font-size:40px;letter-spacing:2.5px;">EXPECTATIONS</p>
  <p class="wide" style="left:40px;top:384px;font-size:36px;letter-spacing:2px;">RESPECT <span class="small" style="font-size:14px;letter-spacing:1.5px">THE LIMITS OF</span></p>
  <p class="wide small" style="left:40px;top:418px;font-size:14px;letter-spacing:1.5px;line-height:1.15;">PEOPLE'S KNOWLEDGE &amp; SHARE YOUR<br>KNOWLEDGE GENEROUSLY.</p>
  <p class="narrow" style="left:40px;top:462px;font-size:44px;font-weight:500;">LEARN SOMETHING</p>
  <p class="narrow" style="left:40px;top:500px;font-size:54px;font-weight:500;letter-spacing:1px;">NEW EACH DAY.</p>

  <p class="wide" style="left:312px;top:226px;font-size:20px;letter-spacing:1.5px;">LOOK AFTER <span style="font-size:46px">YOURSELF</span> &amp;</p>
  <p class="wide small" style="left:312px;top:266px;font-size:20px;line-height:1.15;letter-spacing:3.2px;">VALUE YOUR HEALTH AS MUCH AS<br>YOU VALUE THE HEALTH OF OTHERS.</p>

  <div class="band" style="left:400px;top:336px;width:408px;height:78px;font-size:40px;letter-spacing:3px;line-height:1.0;border-radius:14px;text-align:left;justify-content:flex-start;padding-left:28px;">DELIVER CARE<br>SKILLFULLY.</div>

  <p class="wide" style="left:400px;top:446px;font-size:38px;">SUPPORT <span class="small" style="font-size:18px;letter-spacing:1px">YOUR COLLEAGUES</span></p>
  <p class="wide" style="left:400px;top:476px;font-size:18px;letter-spacing:1px;"><span class="small">&amp; CHAMPION THEIR</span> <span style="font-size:36px">PURPOSE.</span></p>
  <p class="wide small" style="left:400px;top:514px;font-size:14px;letter-spacing:1px;line-height:1.15;">TRUST YOUR KNOWLEDGE &amp; SEEK ADVICE<br>ONLY FROM RESPECTED SOURCES.</p>

  <div class="band" style="left:40px;top:563px;width:768px;height:50px;font-size:46px;letter-spacing:5px;">BE A LIFELONG LEARNER.</div>

  <p class="wide" style="left:40px;top:634px;font-size:50px;letter-spacing:3.5px;line-height:0.9;">CELEBRATE,<br>RESPECT &amp;<br>VALUE</p>
  <svg class="heart-icon" style="left:254px;top:720px" width="106" height="76" viewBox="0 0 128 88" aria-hidden="true">
    <path d="M64 86 C30 62 8 46 8 24 C8 10 20 2 34 2 C48 2 58 12 64 20 C70 12 80 2 94 2 C108 2 120 10 120 24 C120 46 98 62 64 86 Z" fill="var(--white)"/>
    <polyline points="14,42 44,42 50,30 56,56 62,20 68,64 74,36 80,42 114,42" fill="none" stroke="var(--red)" stroke-width="3" stroke-linejoin="round"/>
  </svg>
  <p class="wide small" style="left:40px;top:770px;font-size:15px;letter-spacing:1px;line-height:1.2;">YOU ARE UNIQUE,<br>REVEL IN YOUR</p>
  <p class="wide" style="left:40px;top:806px;font-size:39px;">INDIVIDUALITY.</p>

  <p class="wide" style="left:392px;top:638px;font-size:28px;letter-spacing:3.5px;line-height:1.05;">THE DIVERSITY OF<br>AUSTRALIAN CULTURE.</p>
  <p class="wide" style="left:392px;top:702px;font-size:40px;letter-spacing:2px;">SMILE</p>
  <p class="wide small" style="left:552px;top:704px;width:256px;font-size:16px;letter-spacing:1px;line-height:1.0;text-align:center;">&amp; INFECT OTHERS WITH<br>YOUR</p>
  <p class="wide" style="left:392px;top:737px;font-size:25px;letter-spacing:3.5px;">HAPPINESS &amp; HAVE FUN!</p>
  <p class="wide" style="left:388px;top:776px;font-size:22px;letter-spacing:1.5px;">ALWAYS DO THE</p>
  <p class="wide" style="left:618px;top:770px;font-size:50px;letter-spacing:2px;">RIGHT</p>
  <p class="wide" style="left:388px;top:800px;font-size:50px;letter-spacing:3px;">THING</p>
  <p class="wide small" style="left:598px;top:822px;font-size:16px;letter-spacing:0.5px;">WITHOUT EXCEPTION.</p>

  <p class="wide" style="left:40px;top:860px;font-size:37px;letter-spacing:3px;">SEEK SUCCESS</p>
  <p class="wide" style="left:40px;top:898px;font-size:38px;">FIRSTLY FROM WITHIN.</p>
  <p class="narrow" style="left:386px;top:862px;font-size:32px;font-weight:500;">ALWAYS BE SOLUTION FOCUSED.</p>
  <p class="wide small" style="left:550px;top:908px;width:258px;font-size:17px;letter-spacing:2px;line-height:1.0;text-align:center;">ALWAYS LEAD WITH<br>PURPOSE, PASSION<br>&amp; COMMITMENT.</p>
  <p class="wide" style="left:40px;top:948px;font-size:22px;letter-spacing:1.2px;">ONLY FOLLOW EXCEPTIONAL LEADERS.</p>
  <p class="wide" style="left:40px;top:980px;font-size:22px;letter-spacing:2.3px;">IF THERE IS NO ONE LEFT TO FOLLOW, THEN LEAD!</p>

  <p class="wide small" style="left:40px;top:1016px;font-size:14px;letter-spacing:0.6px;line-height:1.15;">RESPOND TO COMPLEX SITUATIONS INNOVATIVELY,<br>CREATIVELY &amp; SAFELY WITHIN THE SCOPE OF</p>
  <p class="wide" style="left:482px;top:1014px;font-size:36px;letter-spacing:1px;">YOUR PRACTICE.</p>

  <p class="wide small" style="left:40px;top:1070px;font-size:15px;letter-spacing:1px;line-height:1.15;">ADOPT A <span class="wide" style="font-size:26px">'CAN DO'</span><br>ATTITUDE TO EVERYTHING<br>THAT COMES YOUR WAY.</p>
  <p class="narrow" style="left:334px;top:1062px;font-size:33px;font-weight:500;line-height:1.12;">CHOOSE YOUR THOUGHTS WISELY,<br>THEY CREATE YOUR REALITY.</p>

  <div class="band" style="left:40px;top:1141px;width:768px;height:54px;font-size:56px;letter-spacing:9px;">LIVE YOUR DREAM.</div>

</main>
</body>
</html>
```